Victorian Era general store concept

I want to design a Victorian era general store themed web site. I Have existing advertisements from the Harrow Bay Courier from the 1850's that display the Tindle and Corrow brand. I would like to create a logo with that and if the designer can add any anything to it that would enhance the look yet retain its classic Victorian appear that would be great. I will upload the Harrow bay courier publication. Look for Tindle and Corrow ads on there. I would like the design to be simplistic yet classic. Nothing to busy. I would like to add the phrase "A harrow bay orginal" "Est. 1851"
https://www.oldpress-archive.example/library/papers/paper_detail.aspx?t=29
Updates

I am going to upload another file that is very clear. Tindle and Corrow regular line of packets. Hopefully this will help.

Target Market(s)

Undetermined

Industry/Entity Type

Online Store

Number of Pages Required

1 page

Font styles to use
Other font styles liked:
• What is on the adds.

Colors

Designer to choose colors to be used in the design.

Requirements
Must have
• Harrow Bay orginal and est 1851
• Any "Tindle and Corrow" advertisement from the Harrow Bay Courier with details thereof.
Nice to have
• Some type of ship in the logo would be nice if it fits well.

```html
<!DOCTYPE html>
<html lang="en">
<head>
<meta charset="utf-8">
<title>Tindle &amp; Corrow — A Harrow Bay Original</title>
<link href="https://fonts.googleapis.com/css2?family=Cinzel:wght@400;700&family=Montserrat:wght@700&family=Open+Sans:wght@400&display=swap" rel="stylesheet">
<style>
  :root {
    --nav-brown: #523e3b;
    --brand-red: #7a3b32;
    --hero-cream: #efebbf;
    --ink: #2b120e;
    --section-blush: #fcf5f2;
    --card-white: #ffffff;
    --muted-text: #a9a6a5;
    --ribbon-gold: #c9a000;
    --footer-dark: #2b120e;
  }
  * { margin: 0; padding: 0; box-sizing: border-box; }
  html, body { width: 1200px; height: 1183px; overflow: hidden; }
  body { position: relative; background: var(--section-blush); font-family: "Open Sans", sans-serif; }

  .site-nav { position: absolute; top: 0; left: 0; width: 1200px; height: 74px; background: var(--nav-brown); z-index: 2; }
  .site-nav a { position: absolute; top: 30px; color: #fff; text-decoration: none; font-family: "Cinzel", serif; font-weight: 700; font-size: 12px; line-height: 1; }
  .brand-box { position: absolute; left: 518px; top: 0; width: 165px; height: 108px; background: var(--card-white); box-shadow: 0 2px 4px rgba(0,0,0,.15); display: flex; align-items: center; justify-content: center; z-index: 3; }
  .brand-name { font-family: "Cinzel", serif; font-weight: 700; font-size: 17px; line-height: 1; color: var(--brand-red); text-align: center; }

  .hero { position: absolute; top: 74px; left: 0; width: 1200px; height: 608px; background: var(--hero-cream); }
  .hero-frame { position: absolute; left: 288px; top: 99px; width: 624px; height: 410px; border-radius: 50%; background: radial-gradient(ellipse at center, rgba(122,59,50,0) 55%, rgba(122,59,50,.16) 72%, rgba(122,59,50,0) 82%); }
  .hero-text { position: absolute; left: 0; width: 1200px; text-align: center; color: var(--ink); }
  .hero-kicker { top: 252px; font-family: "Montserrat", sans-serif; font-weight: 700; font-size: 15px; }
  .hero-title { top: 278px; font-family: "Cinzel", serif; font-weight: 700; font-size: 46px; line-height: 1.1; }
  .hero-sub { top: 345px; font-family: "Montserrat", sans-serif; font-weight: 700; font-size: 16px; letter-spacing: 9px; padding-left: 9px; }
  .hero-est { top: 380px; font-family: "Cinzel", serif; font-weight: 700; font-size: 11px; letter-spacing: 1px; }
  .hero-year { top: 393px; font-family: "Cinzel", serif; font-weight: 700; font-size: 18px; letter-spacing: 3px; }

  .shipping-title { position: absolute; top: 724px; left: 0; width: 1200px; text-align: center; font-family: "Cinzel", serif; font-weight: 700; font-size: 19px; color: var(--ink); }
  .divider { position: absolute; left: 494px; top: 748px; }

  .ship-card { position: absolute; top: 800px; width: 511px; height: 261px; background: var(--card-white); }
  .card-photo { position: absolute; left: 0; top: 0; width: 256px; height: 261px; overflow: hidden; }
  .photo-ship { background: linear-gradient(180deg, #9fb8d2 0%, #c5d3e0 35%, #dfe4ea 55%, #2b5a85 75%, #1d4266 100%); }
  .photo-trunk { background: linear-gradient(160deg, #1f4a55 0%, #2e5f6a 40%, #6b4a35 70%, #3a2418 100%); }
  .ribbon { position: absolute; left: -48px; top: 34px; width: 230px; height: 28px; background: var(--ribbon-gold); transform: rotate(-35deg); color: #fff; font-family: "Cinzel", serif; font-weight: 700; font-size: 11px; line-height: 28px; text-align: center; }
  .card-body { position: absolute; left: 284px; top: 40px; width: 200px; }
  .card-title { font-family: "Cinzel", serif; font-weight: 700; font-size: 19.5px; line-height: 26px; color: var(--ink); }
  .card-text { margin-top: 17px; font-size: 12.5px; line-height: 14.6px; color: var(--muted-text); }
  .card-link { position: absolute; left: 284px; top: 225px; font-size: 12.5px; color: var(--ink); text-decoration: underline; }

  .site-footer { position: absolute; top: 1105px; left: 0; width: 1200px; height: 78px; background: var(--footer-dark); color: #fff; font-size: 13px; text-align: center; line-height: 78px; }
</style>
</head>
<body>
  <nav class="site-nav">
    <a href="#" style="left:195px">New Arrivals</a>
    <a href="#" style="left:304px">Shipping</a>
    <a href="#" style="left:377px">Kids</a>
    <a href="#" style="left:771px">Jewelry</a>
    <a href="#" style="left:855px">Found</a>
    <a href="#" style="left:923px">Apparell</a>
  </nav>
  <div class="brand-box"><span class="brand-name">Tindle &amp;<br>Corrow</span></div>

  <header class="hero">
    <div class="hero-frame" role="img" aria-label="Ornate Victorian flourish frame in deep brown"></div>
    <p class="hero-text hero-kicker">A</p>
    <h1 class="hero-text hero-title">Harrow Bay</h1>
    <p class="hero-text hero-sub">ORIGINAL</p>
    <p class="hero-text hero-est">Est</p>
    <p class="hero-text hero-year">1851</p>
  </header>

  <h2 class="shipping-title">SHIPPING</h2>
  <svg class="divider" width="212" height="22" viewBox="0 0 212 22" aria-hidden="true">
    <line x1="6" y1="9" x2="206" y2="9" stroke="#2b120e" stroke-width="1"/>
    <path d="M2 9 L6 5 L10 9 L6 13 Z M202 9 L206 5 L210 9 L206 13 Z" fill="#2b120e"/>
    <path d="M94 9 L100 6 L106 9 L100 12 Z M118 9 L112 6 L106 9 L112 12 Z M106 2 L109 9 L106 20 L103 9 Z" fill="#2b120e"/>
  </svg>

  <article class="ship-card" style="left:77px">
    <div class="card-photo photo-ship" role="img" aria-label="Large passenger ship sailing on open blue water">
      <div class="ribbon">First Class Vessel</div>
    </div>
    <div class="card-body">
      <h3 class="card-title">San Fransico<br>&amp; Harrow Bay</h3>
      <p class="card-text">Sed ut perspiciatis unde omnis iste natus error sit voluptatem accusantium doloremque laudan-tium, totam rem aperiam, eaque ipsa quae ab illo inventore verita-tis et quasi architecto beatae vitae</p>
    </div>
    <a class="card-link" href="#">Learn More</a>
  </article>

  <article class="ship-card" style="left:614px">
    <div class="card-photo photo-trunk" role="img" aria-label="Old leather trunk with keepsakes and a framed portrait">
      <div class="ribbon">First Class Vessel</div>
    </div>
    <div class="card-body">
      <h3 class="card-title">Lorem Ipsum<br>&amp; Polor Sit Amet</h3>
      <p class="card-text">Sed ut perspiciatis unde omnis iste natus error sit voluptatem accusantium doloremque laudan-tium, totam rem aperiam, eaque ipsa quae ab illo inventore verita-tis et quasi architecto beatae vitae</p>
    </div>
    <a class="card-link" href="#">Learn More</a>
  </article>

  <footer class="site-footer">Tindle and corrow 2018. All rights Reserved</footer>
</body>
</html>
```